Quillmere Supply Chain and Logistic Consulting

Please review the attached Business Card. I want as close to this card with the colors, fonts, and quality of the card as possible. The attached compass should replace the deer head on both sides of the card and the text should say:

Backside
Compass JPEG
Quillmere SC&L
A Supply Chain and Logistics Consulting Company

Frontside
Quillmere SC&L
Ray Falkner - Tampa Florida
President
____________________________________
(555) 314-9027
QuillmereSCL@Examplemail.com
_____________________________________

Bottom Front Side

Target Market(s)

Businesses

Contact Information for Business Card

Backside
Compass JPEG
Quillmere SC&L

Frontside
Quillmere SC&L
President
(555) 314-9027
QuillmereSCL@Examplemail.com

Bottom Front Side

Font styles to use
Serif
Script

Colors

Designer to choose colors to be used in the design.

Requirements
Must have
• See attached card for reference
Nice to have
Should not have

```html
<!DOCTYPE html>
<html lang="en">
<head>
<meta charset="utf-8">
<title>Quillmere SC&amp;L – Business Card</title>
<link rel="stylesheet" href="https://fonts.googleapis.com/css2?family=Cinzel:wght@400;600&family=Tinos:wght@400;700&display=swap">
<style>
  :root {
    --navy: #0c2b4b;
    --navy-soft: #2f4d70;
    --steel: #6f86a3;
    --mist: #d9e0e8;
    --paper: #ffffff;
    --ink-grey: #4a4f57;
    --rule: #b9bec5;
    --backdrop: #dcdcdc;
  }
  * { margin: 0; padding: 0; box-sizing: border-box; }
  html, body { width: 1200px; height: 900px; overflow: hidden; }
  body {
    background: var(--backdrop);
    position: relative;
    font-family: "Tinos", "Times New Roman", serif;
  }
  .card {
    position: absolute;
    top: 302px;
    width: 520px;
    height: 297px;
    border-radius: 26px;
    overflow: hidden;
  }
  /* Back side */
  .card--back {
    left: 40px;
    background: var(--navy);
    color: var(--paper);
    text-align: center;
  }
  .back-mark {
    position: absolute;
    left: 50%;
    top: 34px;
    transform: translateX(-50%);
    display: flex;
    flex-direction: column;
    align-items: center;
    gap: 8px;
  }
  .back-mark__circle {
    width: 86px; height: 86px;
    border-radius: 50%;
    border: 2px solid var(--paper);
  }
  .back-mark__name {
    font-family: "Cinzel", serif;
    font-size: 13px;
    letter-spacing: 2px;
  }
  .back-title {
    position: absolute;
    left: 0; right: 0; top: 178px;
    font-family: "Cinzel", serif;
    font-weight: 600;
    font-size: 27px;
    letter-spacing: 1.5px;
  }
  .back-tagline {
    position: absolute;
    left: 0; right: 0; top: 226px;
    font-family: "Cinzel", serif;
    font-size: 15px;
    letter-spacing: 0.5px;
  }
  /* Front side */
  .card--front {
    left: 640px;
    background: var(--paper);
    color: var(--navy);
  }
  .front-circle {
    position: absolute;
    right: -70px; top: -80px;
    width: 230px; height: 230px;
    border-radius: 50%;
    background: radial-gradient(circle, var(--steel) 0%, var(--mist) 70%);
  }
  .front-title {
    position: absolute;
    left: 30px; top: 96px;
    font-family: "Cinzel", serif;
    font-weight: 600;
    font-size: 33px;
    letter-spacing: 1.5px;
  }
  .front-location {
    position: absolute;
    left: 170px; top: 138px;
    font-weight: 700;
    font-size: 17px;
  }
  .front-rule {
    position: absolute;
    left: 30px; width: 400px;
    height: 1px; background: var(--rule);
  }
  .front-rule--top { top: 164px; }
  .front-rule--bottom { top: 250px; }
  .contact { position: absolute; left: 30px; top: 172px; }
  .contact__name { font-weight: 700; font-size: 16px; line-height: 18px; }
  .contact__role { font-size: 14px; color: var(--ink-grey); line-height: 17px; }
  .contact__line {
    display: flex; align-items: center; gap: 5px;
    font-size: 15px; color: var(--ink-grey); line-height: 18px;
  }
  .contact__line svg { width: 13px; height: 13px; fill: var(--navy); }
  .front-tagline {
    position: absolute;
    left: 30px; top: 256px;
    font-family: "Cinzel", serif;
    font-size: 13px;
    line-height: 16px;
    letter-spacing: 0.4px;
  }
</style>
</head>
<body>
  <section class="card card--back" aria-label="Back of business card">
    <div class="back-mark">
      <div class="back-mark__circle"></div>
      <span class="back-mark__name">Quillmere</span>
    </div>
    <h1 class="back-title">QUILLMERE SC&amp;L</h1>
    <p class="back-tagline">A Supply Chain and Logistics Consulting Company</p>
  </section>

  <section class="card card--front" aria-label="Front of business card">
    <div class="front-circle"></div>
    <h2 class="front-title">QUILLMERE SC&amp;L</h2>
    <p class="front-location">Ray Falkner - Tampa Florida</p>
    <div class="front-rule front-rule--top"></div>
    <div class="contact">
      <p class="contact__name">Ray Falkner</p>
      <p class="contact__role">President</p>
      <p class="contact__line">
        <svg viewBox="0 0 16 16" aria-hidden="true"><path d="M3.5 1.5l2.5 3-1.5 2c1 2 2.5 3.5 4.5 4.5l2-1.5 3 2.5-1.5 2.5C7 14.5 1.5 9 1 3z"/></svg>
        (555) 314-9027
      </p>
      <p class="contact__line">
        <svg viewBox="0 0 16 16" aria-hidden="true"><path d="M1 3h14v10H1z M2 4l6 5 6-5" stroke="#fff" stroke-width="1"/></svg>
        QuillmereSCL@Examplemail.com
      </p>
    </div>
    <div class="front-rule front-rule--bottom"></div>
    <p class="front-tagline">A Supply Chain and Logistics<br>Consulting Company</p>
  </section>
</body>
</html>
```